Recruitment Site Design

We need a design for the login page, about page, and inner pages of a recruitment site for an oil and gas company. Design should be modern, sleek, professional and colors can be blue, green, white, orange or any other recommended colors.

Please also take into consideration that once the users login, they will need to access a form to fill in their information.

** UPDATE: Kindly provide a design for the inner information page consistent with the outer design. Attached is a picture of the basic structure. ***
Updates

Please provide a design for inner pages as shown in the design brief consistent with the registration page provided. 

Reason: We're extending it to get more inside pages.

Target Market(s)

Professionals looking for a career in the oil and gas industry in the Middle East.

Industry/Entity Type

Oil And Gas

Requirements
Must have
• Sleek design

```html
<!DOCTYPE html>
<html lang="en">
<head>
<meta charset="utf-8">
<title>Petrova – Jobs in Oil &amp; Gas</title>
<link href="https://fonts.googleapis.com/css2?family=Anton&family=Source+Sans+3:wght@400;600;700&family=Arimo:wght@400&display=swap" rel="stylesheet">
<style>
:root{
  --green-light:#74b52c;
  --green-mid:#5c9c20;
  --green-dark:#3f7514;
  --banner:#2f5512;
  --gold-top:#e8b52a;
  --gold-bottom:#c98d0e;
  --brown-top:#4a2c24;
  --brown-bottom:#2a1611;
  --brown-ink:#4b231a;
  --btn:#3d1f17;
  --white:#ffffff;
  --text:#2b2b2b;
  --muted:#555;
  --yellow:#fff25a;
}
*{margin:0;padding:0;box-sizing:border-box}
html,body{width:1200px;height:1185px;overflow:hidden}
body{position:relative;font-family:"Arimo",Arial,sans-serif;background:var(--brown-bottom)}
.abs{position:absolute}
.top{left:0;top:0;width:1200px;height:582px;background:radial-gradient(ellipse at 50% 30%,var(--green-light),var(--green-mid) 60%,var(--green-dark))}
.divider{left:0;top:582px;width:1200px;height:7px;background:#2a1b14}
.main{left:0;top:589px;width:1200px;height:542px;background:linear-gradient(var(--brown-top),var(--brown-bottom))}
.footer{left:0;top:1131px;width:1200px;height:54px;background:linear-gradient(var(--green-light),var(--green-mid))}
.brand{left:187px;top:36px;font-family:"Source Sans 3",sans-serif;font-weight:700;font-size:46px;color:var(--white);letter-spacing:1px}
.nav{left:360px;top:35px;width:659px;height:62px;border-radius:5px;background:linear-gradient(var(--gold-top),var(--gold-bottom));box-shadow:0 2px 3px rgba(0,0,0,.25);display:flex;justify-content:space-around;align-items:center;padding:0 35px;font-family:"Source Sans 3",sans-serif;font-size:16px;color:var(--white)}
.hero-frame{left:189px;top:123px;width:518px;height:321px;background:var(--white);border-radius:4px;padding:7px}
.hero-photo{width:100%;height:100%;border-radius:3px;background:radial-gradient(ellipse at 55% 50%,#e9b22a,#b0581a 45%,#4a2336 90%)}
.hero-title{left:740px;top:172px;font-family:"Anton",sans-serif;font-size:44px;line-height:43px;color:var(--white)}
.hero-sub{left:740px;top:268px;font-family:"Anton",sans-serif;font-size:18px;color:var(--yellow)}
.hero-text{left:740px;top:302px;width:275px;font-size:10.5px;line-height:12.5px;color:var(--white)}
.search{left:740px;top:350px;width:267px;height:35px;background:var(--white);border-radius:3px;display:flex;align-items:center}
.search span{flex:1;padding-left:18px;font-size:10.5px;color:#777;letter-spacing:.5px}
.search .go{width:37px;height:100%;border-left:1px solid #ddd;display:flex;align-items:center;justify-content:center}
.banner{left:186px;top:465px;width:832px;height:87px;background:var(--banner);opacity:.92;border-radius:4px;padding:20px 22px;font-family:"Source Sans 3",sans-serif;font-size:17.5px;line-height:21px;color:var(--white)}
.tab{background:var(--white);border-radius:5px 5px 0 0;font-family:"Anton",sans-serif;color:var(--brown-ink);padding-left:24px}
.more{background:var(--white);border-radius:4px 4px 0 0;font-family:"Source Sans 3",sans-serif;font-weight:600;font-size:13px;color:var(--brown-ink);text-align:center;line-height:24px}
.panel{background:var(--white);border-radius:6px}
.job{position:absolute;width:390px;height:94px}
.thumb{position:absolute;left:0;top:0;width:102px;height:94px;border-radius:8px;border:2px solid #cfcfcf;background:linear-gradient(135deg,#c9d0d8,#7f8a96 50%,#e07a22 75%,#4a4f58)}
.job-body{position:absolute;left:112px;top:4px;width:290px}
.job-name{font-family:"Source Sans 3",sans-serif;font-size:17px;font-weight:600;color:var(--brown-ink);line-height:20px}
.job-loc{font-family:"Source Sans 3",sans-serif;font-size:12.5px;color:var(--brown-ink);line-height:17px}
.job-desc{font-size:10.5px;line-height:12.5px;color:#222;margin-top:3px}
.btns{margin-top:7px;display:flex;gap:5px}
.btn{background:var(--btn);color:var(--white);border-radius:3px;font-family:"Source Sans 3",sans-serif;font-size:11px;height:19px;line-height:19px;padding:0 13px}
.body-copy{font-size:10.5px;line-height:12.6px;color:var(--muted);text-align:justify}
.portrait{left:643px;top:980px;width:91px;height:86px;border-radius:6px;border:3px solid #e4e4e4;background:linear-gradient(#3a5a7a,#b3a08a 60%,#2d3b52)}
.copyright{left:177px;top:1151px;font-size:10.5px;color:#1e2a0c}
.social{left:896px;top:1144px;display:flex;gap:3px}
.social span{width:29px;height:29px;border-radius:4px;background:#2e2a29}
</style>
</head>
<body>
<div class="abs top"></div>
<div class="abs divider"></div>
<div class="abs main"></div>
<div class="abs footer"></div>

<div class="abs brand">Petrova</div>
<nav class="abs nav"><span>About us</span><span>Jobs</span><span>Blog</span><span>Find Now</span><span>Location</span><span>Contact</span></nav>

<div class="abs hero-frame"><div class="hero-photo" role="img" aria-label="Oil refinery lit at night"></div></div>
<h1 class="abs hero-title">Job in Oil &amp;<br>Gas Industry</h1>
<div class="abs hero-sub">Apply Now For Middle East Jobs</div>
<p class="abs hero-text">Lorem ipsum dolor sit amet, consectetuer adipiscing elit. Aenean commodo ligula eget dolor. Aenean massa. natoque penatibus et magnis</p>
<div class="abs search"><span>Type your job for search</span><div class="go"><svg width="18" height="12" viewBox="0 0 18 12"><path d="M1 6h14M10 1l5 5-5 5" stroke="#aaa" stroke-width="2" fill="none"/></svg></div></div>

<div class="abs banner">Lorem ipsum dolor sit amet, consectetuer adipiscing elit. Aenean commodo ligula eget dolor Aenean hew Cum sociis ulus mus. Donec quam felis, ultricies nec natoque penatibus.</div>

<div class="abs tab" style="left:194px;top:614px;width:152px;height:40px;font-size:21px;line-height:40px">Recent Jobs</div>
<div class="abs more" style="left:915px;top:629px;width:93px;height:24px">View More</div>
<section class="abs panel" style="left:178px;top:652px;width:847px;height:242px">
  <div class="job" style="left:21px;top:19px"><div class="thumb" role="img" aria-label="Engineer reviewing plans at a plant"></div><div class="job-body"><div class="job-name">Job Name</div><div class="job-loc">Location: Chennai</div><p class="job-desc">Lorem ipsum dolor sit amet, consectetuer adipiscing magnis dis parturient montes, Aenean commodo.</p><div class="btns"><span class="btn">Apply</span><span class="btn">Details</span></div></div></div>
  <div class="job" style="left:455px;top:19px"><div class="thumb" role="img" aria-label="Engineer reviewing plans at a plant"></div><div class="job-body"><div class="job-name">Job Name</div><div class="job-loc">Location: Chennai</div><p class="job-desc">Lorem ipsum dolor sit amet, consectetuer adipiscing magnis dis parturient montes, Aenean commodo.</p><div class="btns"><span class="btn">Apply</span><span class="btn">Details</span></div></div></div>
  <div class="job" style="left:21px;top:131px"><div class="thumb" role="img" aria-label="Engineer reviewing plans at a plant"></div><div class="job-body"><div class="job-name">Job Name</div><div class="job-loc">Location: Chennai</div><p class="job-desc">Lorem ipsum dolor sit amet, consectetuer adipiscing magnis dis parturient montes, Aenean commodo.</p><div class="btns"><span class="btn">Apply</span><span class="btn">Details</span></div></div></div>
  <div class="job" style="left:455px;top:131px"><div class="thumb" role="img" aria-label="Engineer reviewing plans at a plant"></div><div class="job-body"><div class="job-name">Job Name</div><div class="job-loc">Location: Chennai</div><p class="job-desc">Lorem ipsum dolor sit amet, consectetuer adipiscing magnis dis parturient montes, Aenean commodo.</p><div class="btns"><span class="btn">Apply</span><span class="btn">Details</span></div></div></div>
</section>

<div class="abs tab" style="left:194px;top:914px;width:270px;height:38px;font-size:21px;line-height:38px">Little About Our Company</div>
<div class="abs more" style="left:490px;top:929px;width:93px;height:22px;line-height:22px">View More</div>
<section class="abs panel" style="left:178px;top:950px;width:422px;height:147px;padding:17px 18px">
  <p class="body-copy">Lorem ipsum dolor sit amet, consectetuer adipiscing elit. Aenean commodo ligula eget dolor. Aenean massa. Cum sociis natoque penatibus et magnis dis parturient montes, nascetur ridiculus mus. Donec quam felis, ultricies nec, pellentesque eu, pretium quis, sem. Nulla consequat massa quis enim. Donec pede justo, fringilla vel, aliquet nec, vulputate eget, arcu. In enim justo, rhoncus ut, imperdiet a, venenatis vitae, justo. Nullam dictum felis eu pede mollis pretium. Integer tincidunt. Cras dapibus. Vivamus elementum semper nisi. Aenean vulputate eleifend tellus. Aenean leo ligula, porttitor eu, consequat vitae, eleifend ac, enim. Aliquam lorem ante.</p>
</section>

<div class="abs tab" style="left:633px;top:914px;width:161px;height:38px;font-size:21px;line-height:38px">Testimonials</div>
<div class="abs more" style="left:914px;top:928px;width:93px;height:23px;line-height:23px">View More</div>
<section class="abs panel" style="left:618px;top:950px;width:407px;height:147px"></section>
<div class="abs portrait" role="img" aria-label="Portrait of a satisfied candidate"></div>
<p class="abs body-copy" style="left:747px;top:1001px;width:246px">Lorem ipsum dolor sit amet, consectetuer adipiscing elit. Aenean commodo ligula eget dolor. Aenean massa. Cum sociis natoque penatibus et magnis dis parturient montes, nascetur ridiculus mus.</p>

<div class="abs copyright">(C) 2012 Northgate Crew Inc. ALL RIGHTS RESERVED</div>
<div class="abs social" aria-label="Social links"><span></span><span></span><span></span><span></span></div>
</body>
</html>
```